Very visible CoWorking Building Sign overlooking downtown LA and 110 freeway

Our building is drab but very visible and in the best location. We need a great sign for our monolith that overlooks downtown LA and the 100 freeway. We are a new CoWorking business and would like to have a few things we do on the sign: private offices, virtual offices, CoWorking Lounge. Everything we have seen is ho-hum. Can you get us noticed? We need people to know what we do and that we are here but in a creative, professional, unique sign.
Target Market(s)
People who have a business in DTLA, remote workers and those who work from home who need a professional address.
Requirements
Must have
- Our logo (which can be somewhat reimagined) which has our address 2417 on it. The three things we focus on: Private Offices, Virtual Offices, CoWorking Lounge. Incorporate some Navy. Readable from several hundred feet away.
Nice to have
- Mural feel? Something inspirational in this crazy COVID times? Graphics? Color block. I like the idea of decorative but it has to be readable as a building sign. The same with the use of colors. Our colors are grays and navy but with a pop of the chartreuse (we have 2 velvet chartreuse chairs in the space). Helpful to view our website: Harborview2417.com.
Should not have
- Not too graffiti. Keep it professional but unique and wow.

```html
<!DOCTYPE html>
<html lang="en">
<head>
<meta charset="utf-8">
<title>2417 Harborview Building Sign</title>
<link rel="stylesheet" href="https://fonts.googleapis.com/css2?family=Montserrat:wght@500;600&display=swap">
<style>
  :root {
    --navy: #163a72;
    --navy-deep: #1b2f5e;
    --green-dark: #0a7a45;
    --green-bright: #00a650;
    --chartreuse: #8cc63f;
    --sign-white: #f7f7f7;
    --stage-top: #c4c4c4;
    --stage-bottom: #f1f1f1;
  }
  * { margin: 0; padding: 0; box-sizing: border-box; }
  html, body {
    width: 720px;
    height: 1200px;
    overflow: hidden;
  }
  body {
    background: linear-gradient(180deg, var(--stage-top), var(--stage-bottom));
    font-family: "Montserrat", Arial, sans-serif;
    position: relative;
  }
  .sign {
    position: absolute;
    left: 60px;
    top: 225px;
    width: 600px;
    height: 750px;
    background: linear-gradient(160deg, #ffffff 0%, var(--sign-white) 60%, #ececec 100%);
    box-shadow: 0 10px 24px rgba(0, 0, 0, 0.28);
    overflow: hidden;
  }
  .brand {
    position: absolute;
    left: 0;
    right: 0;
    top: 62px;
    text-align: center;
    color: var(--navy-deep);
    font-weight: 600;
    line-height: 1;
  }
  .brand-number {
    display: block;
    font-size: 40px;
    letter-spacing: 14px;
    margin-bottom: 10px;
  }
  .brand-name {
    display: block;
    font-size: 64px;
    letter-spacing: 2px;
  }
  .accent-band {
    position: absolute;
    left: 0;
    right: 0;
    top: 250px;
    height: 110px;
    background: linear-gradient(90deg, var(--green-dark) 0%, var(--green-bright) 55%, var(--green-dark) 100%);
    opacity: 0.9;
  }
  .ground-strip {
    position: absolute;
    left: 0;
    right: 0;
    bottom: 0;
    height: 64px;
    background: linear-gradient(90deg, var(--chartreuse) 0%, var(--green-dark) 45%, var(--green-bright) 100%);
  }
  .services {
    list-style: none;
  }
  .service {
    position: absolute;
    left: 49px;
    width: 502px;
    height: 68px;
  }
  .service-bar {
    position: absolute;
    left: 53px;
    right: 0;
    top: 7px;
    height: 54px;
    background: var(--navy);
    border-radius: 0 27px 27px 0;
  }
  .service-label {
    position: absolute;
    left: 84px;
    top: 0;
    line-height: 68px;
    color: #ffffff;
    font-weight: 600;
    font-size: 30px;
    letter-spacing: -0.3px;
    white-space: nowrap;
  }
  .service-icon {
    position: absolute;
    left: 0;
    top: 0;
    width: 68px;
    height: 68px;
  }
  .service--private { top: 392px; }
  .service--virtual { top: 473px; }
  .service--lounge  { top: 554px; }
  .web-address {
    position: absolute;
    left: 0;
    right: 0;
    top: 636px;
    text-align: center;
    color: var(--navy-deep);
    font-weight: 600;
    font-size: 28px;
    letter-spacing: 3px;
  }
</style>
</head>
<body>
  <main class="sign">
    <h1 class="brand">
      <span class="brand-number">2417</span>
      <span class="brand-name">HARBORVIEW</span>
    </h1>

    <div class="accent-band" role="img" aria-label="Decorative band of green geometric shapes"></div>

    <ul class="services">
      <li class="service service--private">
        <span class="service-bar"></span>
        <span class="service-label">PRIVATE OFFICES</span>
        <svg class="service-icon" viewBox="0 0 68 68" aria-hidden="true">
          <circle cx="34" cy="34" r="31" fill="#ffffff" stroke="var(--chartreuse)" stroke-width="4"/>
          <path d="M21 34 H45 M36 25 L45 34 L36 43" fill="none" stroke="var(--navy)" stroke-width="5" stroke-linecap="round" stroke-linejoin="round"/>
        </svg>
      </li>
      <li class="service service--virtual">
        <span class="service-bar"></span>
        <span class="service-label">VIRTUAL OFFICES</span>
        <svg class="service-icon" viewBox="0 0 68 68" aria-hidden="true">
          <circle cx="34" cy="34" r="31" fill="#ffffff" stroke="var(--chartreuse)" stroke-width="4"/>
          <path d="M21 34 H45 M36 25 L45 34 L36 43" fill="none" stroke="var(--navy)" stroke-width="5" stroke-linecap="round" stroke-linejoin="round"/>
        </svg>
      </li>
      <li class="service service--lounge">
        <span class="service-bar"></span>
        <span class="service-label">COWORKING LOUNGE</span>
        <svg class="service-icon" viewBox="0 0 68 68" aria-hidden="true">
          <circle cx="34" cy="34" r="31" fill="#ffffff" stroke="var(--chartreuse)" stroke-width="4"/>
          <path d="M21 34 H45 M36 25 L45 34 L36 43" fill="none" stroke="var(--navy)" stroke-width="5" stroke-linecap="round" stroke-linejoin="round"/>
        </svg>
      </li>
    </ul>

    <p class="web-address">www.harborview2417.com</p>

    <div class="ground-strip" role="img" aria-label="Decorative strip of green and chartreuse geometric shapes"></div>
  </main>
</body>
</html>
```